Business Card Design Project

Looking to update our business cards. We have a logo with our slogan. We are an IT firm so we wouldlike a modern look.

Industry/Entity Type

Business

```html
<!DOCTYPE html>
<html lang="en">
<head>
<meta charset="utf-8">
<title>Corelane Business Card – Front and Back</title>
<link rel="stylesheet" href="https://fonts.googleapis.com/css2?family=Cinzel:wght@600;700&family=Source+Sans+3:wght@400;600&display=swap">
<style>
  :root {
    --stage-light: #f4f4f4;
    --stage-mid: #d2d2d2;
    --stage-dark: #a9a9a9;
    --card-white: #ffffff;
    --card-black: #000000;
    --brand-green: #5a9a1e;
    --deep-navy: #07101c;
    --ink: #111111;
    --paper-text: #ffffff;
  }
  * { box-sizing: border-box; margin: 0; padding: 0; }
  html, body {
    width: 1015px;
    height: 1200px;
    overflow: hidden;
  }
  body {
    position: relative;
    background: radial-gradient(ellipse 60% 55% at 50% 52%, var(--stage-light) 0%, var(--stage-mid) 60%, var(--stage-dark) 100%);
    font-family: "Source Sans 3", Arial, sans-serif;
  }

  .side-label {
    position: absolute;
    font-family: "Cinzel", "Times New Roman", serif;
    font-weight: 700;
    font-size: 50px;
    color: var(--ink);
    line-height: 1;
  }
  .side-label--front { left: 756px; top: 322px; }
  .side-label--back  { left: 118px; top: 800px; }

  /* Front */
  .card-front {
    position: absolute;
    left: 99px;
    top: 180px;
    width: 623px;
    height: 418px;
    background: var(--card-white);
    border: 2px solid var(--card-white);
    overflow: hidden;
  }
  .brand {
    position: absolute;
    left: 0;
    top: 0;
    width: 100%;
    height: 181px;
    display: flex;
    flex-direction: column;
    align-items: center;
    justify-content: center;
    gap: 6px;
  }
  .brand__row {
    display: flex;
    align-items: center;
    gap: 12px;
  }
  .brand__dot {
    width: 20px;
    height: 20px;
    border-radius: 50%;
    background: var(--brand-green);
  }
  .brand__name {
    font-family: "Source Sans 3", Arial, sans-serif;
    font-weight: 600;
    font-size: 46px;
    letter-spacing: 8px;
    color: var(--brand-green);
    line-height: 1;
  }
  .brand__tagline {
    font-family: "Source Sans 3", Arial, sans-serif;
    font-weight: 600;
    font-size: 12px;
    letter-spacing: 3.2px;
    color: var(--brand-green);
  }
  .front-visual {
    position: absolute;
    left: 0;
    top: 181px;
    width: 100%;
    height: 235px;
    background:
      radial-gradient(ellipse 35% 30% at 55% 52%, rgba(160, 230, 60, 0.75) 0%, rgba(80, 170, 40, 0.35) 45%, rgba(0,0,0,0) 100%),
      radial-gradient(ellipse 30% 25% at 82% 78%, rgba(120, 180, 220, 0.35) 0%, rgba(0,0,0,0) 100%),
      radial-gradient(ellipse 60% 50% at 40% 55%, rgba(30, 90, 60, 0.6) 0%, rgba(0,0,0,0) 100%),
      var(--deep-navy);
  }

  /* Back */
  .card-back {
    position: absolute;
    left: 319px;
    top: 627px;
    width: 625px;
    height: 411px;
    background: var(--card-black);
    color: var(--paper-text);
  }
  .card-back__corner {
    position: absolute;
  }
  .card-back__corner--top { left: 19px; top: 16px; }
  .card-back__corner--bottom { left: 561px; top: 329px; }

  .holder {
    position: absolute;
    left: 0;
    top: 128px;
    width: 100%;
    text-align: center;
    font-family: "Cinzel", "Times New Roman", serif;
    font-weight: 700;
    line-height: 1;
  }
  .holder__name { font-size: 36px; letter-spacing: 0.5px; }
  .holder__role { font-size: 24px; margin-top: 9px; }

  .contact {
    position: absolute;
    font-size: 15.5px;
    line-height: 24px;
  }
  .contact--left { left: 30px; top: 338px; }
  .contact--right { left: 400px; top: 345px; }
  .contact__label {
    font-family: "Cinzel", "Times New Roman", serif;
    font-weight: 700;
    font-size: 16px;
  }
</style>
</head>
<body>

  <div class="side-label side-label--front">Front</div>
  <div class="side-label side-label--back">Back</div>

  <section class="card-front" aria-label="Card front">
    <div class="brand">
      <div class="brand__row">
        <span class="brand__dot"></span>
        <span class="brand__name">CORELANE</span>
      </div>
      <div class="brand__tagline">MAKING TECHNOLOGY SIMPLE</div>
    </div>
    <div class="front-visual" role="img" aria-label="Abstract digital illustration of glowing green circuit lines and light particles on a dark navy background"></div>
  </section>

  <section class="card-back" aria-label="Card back">
    <svg class="card-back__corner card-back__corner--top" width="42" height="56" viewBox="0 0 42 56">
      <path d="M1.5 56 V1.5 H42" fill="none" stroke="var(--brand-green)" stroke-width="3"/>
    </svg>
    <svg class="card-back__corner card-back__corner--bottom" width="42" height="56" viewBox="0 0 42 56">
      <path d="M0 54.5 H40.5 V0" fill="none" stroke="var(--brand-green)" stroke-width="3"/>
    </svg>

    <div class="holder">
      <div class="holder__name">YOUR NAME HERE</div>
      <div class="holder__role">YOUR POSITION</div>
    </div>

    <div class="contact contact--left">
      <div><span class="contact__label">Email :</span> yourname@xxx.com</div>
      <div><span class="contact__label">Web</span> : www.websitename.com</div>
    </div>
    <div class="contact contact--right">
      <div><span class="contact__label">Phone :</span> 00-11-222-3333</div>
      <div><span class="contact__label">Fax:</span> 00-11-222-3333</div>
    </div>
  </section>

</body>
</html>
```